KorvaNest - Home Income and Business Resources Platform

I am looking for a website template for a multi-purposed website. This website will feature:

1.) Website Directory with Ratings & comments on listings
2.) Company Blog
3.) Homepage with Content (see files for homepage mock)

I would like the Design to have a default width 1170px (wider then normal)

Of course I am looking for Pages for Listings to be designed.

Great looking BLOG Layout: http://journal.plimworks.example/html/blog.html

I would like 4 Versions of a Website Directory Listing "Box"
1.) Basic Listing Box
2.) Sponsored Listing Box
3.) Recommended Listing Box
4.) Stay Away From Listing Box

Information on the Listing Page (Like on a Category Page)
Site Name, Site URL, Website Image, # of Views, Rating and # of Comments

Information on the Listing Details Page:
Same as ABOVE + About website Description, Vornic Score, Category Information

Decent looking examples is here: https://samples.trevolin.example/directory/computers/ and http://www.zqrankhub.example/.

I will include some sketches and screenshots of things I like/looking for. As designers,you have creative freedom and are encouraged to show this. This is Phase one of this project and winning designer is guaranteed to have future work for this project.

Target Market(s)

Directory, business, websites

Industry/Entity Type

Business

Coding

Coded - Design and coding required

Number of Pages Required

5+ page

Font styles to use
Sans Serif

Colors

Designer to choose colors to be used in the design.

Requirements
Must have
• Professional yet clean look. The use of Icons & images
• Unique Look
Should not have
• Any exact copies of any examples I provided

```html
<!DOCTYPE html>
<html lang="en">
<head>
<meta charset="utf-8">
<title>KorvaNest – Home Income and Business Resources</title>
<link href="https://fonts.googleapis.com/css2?family=Raleway:wght@300;400;500;600;700&family=Open+Sans:wght@400;600&display=swap" rel="stylesheet">
<style>
:root{
  --blue:#1a6fd6;
  --blue-text:#1c73c9;
  --link:#1a9ad6;
  --orange:#ff6a0c;
  --ink:#222;
  --body:#333;
  --muted:#777;
  --line:#d2d2d2;
  --panel:#f7f7f7;
  --box-border:#7fb1e6;
  --white:#fff;
}
*{box-sizing:border-box;margin:0;padding:0}
html,body{width:1200px;height:2323px;overflow:hidden;background:var(--white)}
body{position:relative;font-family:"Raleway",sans-serif;color:var(--body)}
.abs{position:absolute}

/* header */
.brand{left:73px;top:8px}
.brand-name{font-family:"Raleway",sans-serif;font-weight:600;font-size:19px;color:var(--blue-text);line-height:22px}
.brand-tag{font-size:10px;color:var(--ink);line-height:12px}
.phone{right:75px;top:14px;font-size:15px;color:#444;display:flex;align-items:center;gap:6px;font-family:"Open Sans",sans-serif}
.nav{left:73px;top:46px;width:1052px;height:35px;background:var(--blue);display:flex;align-items:center;padding:0 14px;justify-content:space-between}
.nav ul{list-style:none;display:flex;gap:18px}
.nav a{color:var(--white);text-decoration:none;font-size:13px;font-weight:600;text-transform:uppercase}
.nav .social{display:flex;gap:14px}
.dot{width:10px;height:10px;background:var(--white);border-radius:2px;display:block}

/* hero */
.hero{left:73px;top:96px;width:1052px;height:353px;background:linear-gradient(120deg,#6f7b85 0%,#b9c2c6 40%,#9aa3a6 65%,#6d6a66 100%);box-shadow:0 14px 16px -10px rgba(0,0,0,.35)}
.hero-card{left:104px;top:129px;width:294px;height:294px;border-radius:50%;background:var(--white);border:2px solid var(--blue);box-shadow:0 0 0 6px rgba(255,255,255,.55);text-align:center;padding:62px 36px 0}
.hero-card h1{font-weight:400;font-size:18px;line-height:24px;color:var(--blue-text)}
.hero-card hr{border:0;border-top:1px solid #999;width:150px;margin:10px auto}
.hero-card p{font-size:11px;line-height:15px;color:#444}
.btn{display:inline-flex;align-items:center;justify-content:center;color:var(--white);font-size:13px;font-weight:500;text-decoration:none}
.btn-orange{background:var(--orange)}
.btn-blue{background:var(--blue)}
.hero-card .btn{width:140px;height:36px;margin-top:14px;font-size:15px}

/* feature boxes */
.feature{top:517px;width:211px;height:619px;border:1px solid var(--box-border);border-radius:4px;padding:22px 10px 0 11px}
.feature-icon{height:38px}
.feature h2{font-weight:400;font-size:17px;line-height:24px;color:var(--blue-text);height:52px;display:flex;align-items:flex-end;margin-top:6px}
.feature p{font-family:"Open Sans",sans-serif;font-size:12.2px;line-height:20px;color:var(--ink);margin-top:10px;height:400px;overflow:hidden}
.feature .btn{position:absolute;left:9px;bottom:19px;width:148px;height:34px}

/* posts */
.post-photo{left:73px;width:240px;height:331px}
.post{left:330px;width:390px;text-align:center}
.post h3{font-weight:400;font-size:20px;line-height:24px;color:var(--ink);padding:0 40px}
.post .rule{width:44px;height:2px;background:var(--ink);margin:8px auto 6px}
.post .cats{font-size:11px;font-weight:600;color:var(--blue-text)}
.post p{text-align:left;font-size:12.5px;line-height:22px;color:#333;margin-top:18px}
.post .byline{text-align:left;font-size:13px;margin-top:12px;color:#333;padding-bottom:12px;border-bottom:2px solid var(--line)}
.byline span{color:var(--link);font-weight:500;margin:0 6px}
.post .foot{display:flex;justify-content:space-between;align-items:center;padding-top:10px}
.post .foot .btn{width:148px;height:35px}
.counts{display:flex;gap:18px;font-size:11px;color:#444;align-items:center;margin-right:12px}
.counts i{display:inline-flex;align-items:center;gap:5px;font-style:normal}

/* sidebar */
.sidebar{left:763px;top:511px;width:362px;height:1695px;background:var(--panel)}
.side-title{width:362px;left:763px;text-align:center;font-size:20px;color:var(--blue-text);font-weight:400}
.side-rule{left:763px;width:362px;height:2px;background:var(--line)}
.avatar{left:878px;top:543px;width:136px;height:136px;border-radius:50%;background:radial-gradient(circle at 50% 45%,#c9a184,#8b6b58);border:4px solid #ddd}
.about-text{left:785px;top:727px;width:320px;font-size:12.5px;line-height:20px;color:#666}
.socials{left:830px;top:1022px;display:flex;gap:22px}
.socials span{width:28px;height:28px;background:var(--blue);display:block;position:relative}
.socials span::after{content:"";position:absolute;left:9px;bottom:-6px;border:5px solid transparent;border-top-color:var(--blue);border-bottom:0}
.follow{left:763px;width:362px;top:1064px;text-align:center;font-size:11px;color:#333}
.recent-photo{left:780px;width:330px;height:115px}
.recent-title{left:780px;width:330px;text-align:center;font-size:13px;font-weight:600;color:var(--link)}
.recent-date{left:780px;width:330px;text-align:center;font-size:12px;color:#222}
.recent-date::before{content:"";display:block;width:36px;height:2px;background:#222;margin:0 auto 6px}
.arrows{left:919px;top:1573px;display:flex;gap:3px}
.arrows span{width:21px;height:24px;background:var(--orange);display:flex;align-items:center;justify-content:center}
.promo{left:782px;top:1683px;width:326px;height:453px;background:linear-gradient(160deg,#1d1d1d,#0c0c0c 60%,#1a2430);padding:30px 14px 0 14px;color:var(--white);overflow:hidden}
.promo h4{font-weight:300;font-size:54px;line-height:76px;letter-spacing:0}
.promo p{font-family:"Open Sans",sans-serif;font-size:11.5px;line-height:19px;margin-top:14px}

/* footer */
.footer-rule{left:0;top:2291px;width:1200px;height:2px;background:var(--blue)}
.footer{left:73px;top:2302px;width:1052px;display:flex;justify-content:space-between;font-size:11px;color:#666}
.footer nav{display:flex;gap:14px;align-items:center}
.footer a{color:#666;text-decoration:none}
.footer .mini{display:flex;gap:6px;margin-right:10px}
.mini span{width:8px;height:8px;background:#777;display:block;border-radius:1px}
</style>
</head>
<body>

<header>
  <div class="abs brand">
    <div class="brand-name">KorvaNest</div>
    <div class="brand-tag">Home Income and Business Resources</div>
  </div>
  <div class="abs phone">
    <svg width="14" height="14" viewBox="0 0 24 24"><path fill="#555" d="M6.6 10.8a15 15 0 0 0 6.6 6.6l2.2-2.2a1 1 0 0 1 1-.25 11.4 11.4 0 0 0 3.6.57 1 1 0 0 1 1 1V20a1 1 0 0 1-1 1A17 17 0 0 1 3 4a1 1 0 0 1 1-1h3.5a1 1 0 0 1 1 1c0 1.250.2 2.45.57 3.6a1 1 0 0 1-.25 1z"/></svg>
    0800-000-000-000
  </div>
  <nav class="abs nav">
    <ul>
      <li><a href="#">Home</a></li>
      <li><a href="#">About</a></li>
      <li><a href="#">Page Templates</a></li>
      <li><a href="#">Shortcodes</a></li>
      <li><a href="#">Shop Page</a></li>
      <li><a href="#">Contact</a></li>
    </ul>
    <div class="social"><span class="dot"></span><span class="dot"></span><span class="dot"></span></div>
  </nav>
</header>

<section>
  <div class="abs hero" role="img" aria-label="Photo of people working at a laptop with papers and a pencil on a desk"></div>
  <div class="abs hero-card">
    <h1>Home Income<br>and Business Resources</h1>
    <hr>
    <p>Lorem Ipsum is simply dummy text of the printing and typesettin Lorem Ipsum has been the industry's standard dummy text.</p>
    <a class="btn btn-orange" href="#">Read More</a>
  </div>
</section>

<section>
  <article class="abs feature" style="left:71px">
    <svg class="feature-icon" width="48" height="38" viewBox="0 0 48 38"><circle cx="28" cy="12" r="9" fill="none" stroke="#222" stroke-width="2.5"/><path d="M4 26h14l8 4 16-8v4L26 34 4 32z" fill="none" stroke="#222" stroke-width="2.5" stroke-linejoin="round"/></svg>
    <h2>Home Income<br>Resource Directory</h2>
    <p>Text: Find what you need, when you need it.The KorvaNest website directory is your one-stop pit for anything involved in making money from home, marketing your business or finding a new opportunity. Our modern, community supported ectory will help you keep upto toate with the lastest information in a sensibl Lorem Ipsum simply dummy tethe printing and typesetting industry. Lorem Ipsum has been the industry's standard dummy text ever since the Lorem Ipsum is simply dummy text of the printing and typesettin industry. Lorem Ipsum has been the industry's</p>
    <a class="btn btn-orange" href="#">Read More</a>
  </article>
  <article class="abs feature" style="left:300px">
    <svg class="feature-icon" width="40" height="38" viewBox="0 0 40 38"><rect x="5" y="4" width="30" height="20" fill="none" stroke="#222" stroke-width="2.5"/><path d="M11 19v-6M17 19v-9M23 19v-4M29 19V9M20 24v10M12 34h16" stroke="#222" stroke-width="2.5"/></svg>
    <h2>Advertising Benefits</h2>
    <p>Text: Everyone needs to advertise and we know just how to get your offer out to the right people. We have many methods including: Text ads, E-mail, Display, newsletter and even some old school methods available to make your next campaign a success. Advertise a website, a link text, full page circular or a small display ad and get results. Every advertiser recieves a dedicated account manager that will handle everything for You Lorem Ipsum is simply dummy text of the printing and typesetting industry. Lorem Ipsum has been the industry's standard</p>
    <a class="btn btn-blue" href="#">Read More</a>
  </article>
  <article class="abs feature" style="left:529px">
    <svg class="feature-icon" width="48" height="38" viewBox="0 0 48 38"><circle cx="28" cy="12" r="9" fill="none" stroke="#222" stroke-width="2.5"/><path d="M4 26h14l8 4 16-8v4L26 34 4 32z" fill="none" stroke="#222" stroke-width="2.5" stroke-linejoin="round"/></svg>
    <h2>Earning With KorvaNest</h2>
    <p>Text: Join KorvaNest and start earning money. When you share KorvaNest and lock in an advertiser or premium listing, we reward you. Build a downline at any of our listed sites when you share KorvaNest with NO extra work. Its all done for you.We also offer a revenue share program for true supporters of our mission. Lorem Ipsum is simply dummy text of the printing and typesetting industry. Lorem Ipsum has been the industry's standard dummy text ever since theLorem Ipsum is simply dummy text of the printing and typesetting industry. Lorem Ipsum has been the</p>
    <a class="btn btn-orange" href="#">Read More</a>
  </article>
</section>

<main>
  <div class="abs post-photo" style="top:1183px;background:linear-gradient(135deg,#5d6b3c,#c9b8a6 55%,#e7dde0)" role="img" aria-label="Photo of a smiling woman talking on a phone"></div>
  <article class="abs post" style="top:1197px">
    <h3>Chronic Illness and Starting an Exercise Regimen</h3>
    <div class="rule"></div>
    <div class="cats">Daily Living, Health</div>
    <p>Your general health is intimately connected with the foods and drinks you put into your body. Each person is unique in what food or drink can trigger feeling unhealthy and rundown. It is very easy to lose track of which foods and drinks can be wreaking havoc with your health. A great way to do some detective work</p>
    <div class="byline">Written by<span>Mara Elston</span>in<span>August 22, 2016</span></div>
    <div class="foot"><a class="btn btn-orange" href="#">Read More</a>
      <div class="counts"><i><svg width="12" height="11" viewBox="0 0 12 11"><path d="M1 1h10v7H5l-3 3V8H1z" fill="var(--blue)"/></svg>05</i><i><svg width="12" height="11" viewBox="0 0 12 11"><path d="M6 10 1 5a2.6 2.6 0 0 1 5-3 2.6 2.6 0 0 1 5 3z" fill="var(--blue)"/></svg>02</i></div></div>
  </article>

  <div class="abs post-photo" style="top:1560px;background:linear-gradient(160deg,#3a5a8c,#9a8070 60%,#c9bdb0)" role="img" aria-label="Photo of a laptop keyboard on a desk"></div>
  <article class="abs post" style="top:1576px">
    <h3>Chronic Illness and Starting an Exercise Regimen</h3>
    <div class="rule"></div>
    <div class="cats">Daily Living, Health</div>
    <p>Your general health is intimately connected with the foods and drinks you put into your body. Each person is unique in what food or drink can trigger feeling unhealthy and rundown. It is very easy to lose track of which foods and drinks can be wreaking havoc with your health. A great way to do some detective work</p>
    <div class="byline">Written by<span>Mara Elston</span>in<span>August 22, 2016</span></div>
    <div class="foot"><a class="btn btn-blue" href="#">Read More</a>
      <div class="counts"><i><svg width="12" height="11" viewBox="0 0 12 11"><path d="M1 1h10v7H5l-3 3V8H1z" fill="var(--blue)"/></svg>05</i><i><svg width="12" height="11" viewBox="0 0 12 11"><path d="M6 10 1 5a2.6 2.6 0 0 1 5-3 2.6 2.6 0 0 1 5 3z" fill="var(--blue)"/></svg>02</i></div></div>
  </article>

  <div class="abs post-photo" style="top:1935px;background:linear-gradient(150deg,#6b4a34,#b98a66 45%,#d9d4cf)" role="img" aria-label="Photo of hands typing on a laptop beside a coffee cup"></div>
  <article class="abs post" style="top:1950px">
    <h3>Chronic Illness and Starting an Exercise Regimen</h3>
    <div class="rule"></div>
    <div class="cats">Daily Living, Health</div>
    <p>Your general health is intimately connected with the foods and drinks you put into your body. Each person is unique in what food or drink can trigger feeling unhealthy and rundown. It is very easy to lose track of which foods and drinks can be wreaking havoc with your health. A great way to do some detective work</p>
    <div class="byline">Written by<span>Mara Elston</span>in<span>August 22, 2016</span></div>
    <div class="foot"><a class="btn btn-orange" href="#">Read More</a>
      <div class="counts"><i><svg width="12" height="11" viewBox="0 0 12 11"><path d="M1 1h10v7H5l-3 3V8H1z" fill="var(--blue)"/></svg>05</i><i><svg width="12" height="11" viewBox="0 0 12 11"><path d="M6 10 1 5a2.6 2.6 0 0 1 5-3 2.6 2.6 0 0 1 5 3z" fill="var(--blue)"/></svg>02</i></div></div>
  </article>
</main>

<aside>
  <div class="abs sidebar"></div>
  <div class="abs avatar" role="img" aria-label="Portrait photo of the site author"></div>
  <div class="abs side-title" style="top:690px">About Us</div>
  <p class="abs about-text">Lorem Ipsum is simply dummy text of the printing and typesetting industry. Lorem Ipsum has been the industry's standard dummy text ever since the 1500s, when an wn printer took a galley of type and scrambled it to make a type specimen book. Lorem Ipsum is simply dummy text of the printing and type-setting industry. Lorem Ipsum has been the industry's standard dummy text ever since the 1500s, when an unknown printer took a galley of type and</p>

  <div class="abs side-title" style="top:948px">Social Media</div>
  <div class="abs side-rule" style="top:984px"></div>
  <div class="abs socials"><span></span><span></span><span></span><span></span><span></span></div>
  <div class="abs follow">Follow Us</div>

  <div class="abs side-title" style="top:1114px">Recent Posts</div>
  <div class="abs side-rule" style="top:1149px"></div>
  <div class="abs recent-photo" style="top:1176px;background:linear-gradient(120deg,#7a8a3a,#c98f6e 55%,#d9b08a)" role="img" aria-label="Photo of a woman blowing bubbles outdoors"></div>
  <div class="abs recent-title" style="top:1300px">Regular Exercise is a Natural Anti-Inflammatory</div>
  <div class="abs recent-date" style="top:1323px">August 22, 2016</div>
  <div class="abs recent-photo" style="top:1372px;background:linear-gradient(180deg,#8fb5d6,#6f8a5a 60%,#5d6a4a)" role="img" aria-label="Photo of a stone cottage with a garden"></div>
  <div class="abs recent-title" style="top:1497px">Regular Exercise is a Natural Anti-Inflammatory</div>
  <div class="abs recent-date" style="top:1520px">August 22, 2016</div>
  <div class="abs arrows">
    <span><svg width="8" height="10" viewBox="0 0 8 10"><path d="M6 1 2 5l4 4" stroke="#fff" stroke-width="2" fill="none"/></svg></span>
    <span><svg width="8" height="10" viewBox="0 0 8 10"><path d="m2 1 4 4-4 4" stroke="#fff" stroke-width="2" fill="none"/></svg></span>
  </div>

  <div class="abs side-title" style="top:1626px">Hey Warriors, We Support You!</div>
  <div class="abs side-rule" style="top:1663px"></div>
  <div class="abs promo">
    <h4>Advertising Benefits</h4>
    <p>Action plan chronic chronic illness chronic illness pain chronic pain coping with a chronic illness depression employment energy failure fibro fibro-myalgia focus food diary functional medicine goal action plan goals inflammation invisible illness job job hunting life goals live with chronic illness living with long term condition long term condition manage chronic pain meditation natural remedies pain pain control parenting with chronic illness passion quit job resolutions self awareness setback side hustle side hustling SMART goals spoon theory success yoga</p>
  </div>
</aside>

<footer>
  <div class="abs footer-rule"></div>
  <div class="abs footer">
    <nav>
      <div class="mini"><span></span><span></span><span></span></div>
      <a href="#">About Us</a><a href="#">Privacy Policy</a><a href="#">Terms of Use</a><a href="#">Advertise Us</a><a href="#">Help</a>
    </nav>
    <div>© 2017 Copyright</div>
  </div>
</footer>

</body>
</html>
```